Meridale Bed Company Needs Business Card

Looking for a very nice looking business card. Creative but not extravagant. We sell beds and pillows across the U.S. and need something professional but catchy. I have attached the logo.

Name : Devin Holt
Title : President
Phone : (800) 471-2960
Email: sleep@quilmora.com
Website: www.quilmora.com

Can be single-sided or double-sided
horizontal or vertical

Can use Blues/Greys

Target Market(s)

Mass Market

Industry/Entity Type

Retail

Contact Information for Business Card

Name : Devin Holt
Title : President
Phone : (800) 471-2960
Email: sleep@quilmora.com
Website: www.quilmora.com

Requirements
Must have
• Clean, Modern, Smooth
• Can use Blues/Greys
• On the other side without the information - have something simple like www.quilmora.com or our logo
Nice to have
• Surprise me
Should not have
• Nothing crazy, nothing cluttered

```html
<!DOCTYPE html>
<html lang="en">
<head>
<meta charset="utf-8">
<title>Quilmora Business Card</title>
<link href="https://fonts.googleapis.com/css2?family=Open+Sans:wght@300;400;600&display=swap" rel="stylesheet">
<style>
  :root {
    --canvas-bg: #ecebea;
    --front-center: #4d4d4d;
    --front-edge: #262626;
    --back-center: #43b4e6;
    --back-edge: #2f9fd4;
    --ink-light: #ffffff;
    --ink-soft: #e6e6e6;
    --ink-logo: #e2e2e2;
  }
  * { margin: 0; padding: 0; box-sizing: border-box; }
  html, body {
    width: 1200px;
    height: 900px;
    overflow: hidden;
    background: var(--canvas-bg);
    font-family: "Open Sans", Arial, sans-serif;
  }
  .canvas {
    position: relative;
    width: 1200px;
    height: 900px;
  }
  .card {
    position: absolute;
    width: 556px;
    height: 342px;
    box-shadow: 0 6px 18px rgba(0,0,0,0.18);
  }
  .card--front {
    left: 238px;
    top: 62px;
    background: radial-gradient(ellipse at 50% 45%, var(--front-center) 0%, var(--front-edge) 75%);
  }
  .card--back {
    left: 460px;
    top: 518px;
    background: radial-gradient(ellipse at 50% 40%, var(--back-center) 0%, var(--back-edge) 70%);
  }
  .holder {
    position: absolute;
    left: 33px;
    top: 30px;
    color: var(--ink-light);
  }
  .holder__name {
    font-size: 24px;
    font-weight: 600;
    line-height: 32px;
  }
  .holder__title {
    font-size: 20px;
    font-weight: 400;
    line-height: 28px;
    color: var(--ink-soft);
  }
  .wordmark {
    position: absolute;
    left: 0;
    right: 0;
    text-align: center;
    font-weight: 300;
    letter-spacing: 2px;
  }
  .card--front .wordmark {
    top: 118px;
    font-size: 66px;
    line-height: 80px;
    color: var(--ink-logo);
  }
  .card--back .wordmark {
    top: 118px;
    font-size: 76px;
    line-height: 92px;
    color: var(--ink-light);
  }
  .contact {
    position: absolute;
    left: 304px;
    top: 238px;
    list-style: none;
    color: var(--ink-soft);
    font-size: 16px;
    line-height: 23px;
  }
  .contact__item {
    display: flex;
    align-items: center;
  }
  .contact__icon {
    width: 12px;
    height: 12px;
    margin-right: 11px;
    fill: var(--ink-soft);
  }
</style>
</head>
<body>
<main class="canvas">
  <section class="card card--front" aria-label="Business card front">
    <div class="holder">
      <p class="holder__name">Devin Holt</p>
      <p class="holder__title">President</p>
    </div>
    <p class="wordmark">quilmora</p>
    <ul class="contact">
      <li class="contact__item">
        <svg class="contact__icon" viewBox="0 0 12 12" aria-hidden="true"><path d="M2.4 0.6 L4.2 2.6 L3.2 4 C3.8 5.6 5.6 7.6 7.8 8.6 L9.2 7.6 L11.4 9.4 L10.2 11.4 C5.2 11 0.8 6.4 0.6 1.8 Z"/></svg>
        <span>(800) 471-2960</span>
      </li>
      <li class="contact__item">
        <svg class="contact__icon" viewBox="0 0 12 12" aria-hidden="true"><path d="M0.5 2.5 H11.5 V3 L6 6.6 L0.5 3 Z M0.5 4.2 L6 7.8 L11.5 4.2 V9.8 H0.5 Z"/></svg>
        <span>sleep@quilmora.com</span>
      </li>
      <li class="contact__item">
        <svg class="contact__icon" viewBox="0 0 12 12" aria-hidden="true"><circle cx="6" cy="6" r="5.5"/><path d="M3 4 Q5 3 5.5 5 Q4 6.5 5 8 Q3 8 2.5 6 Z M7 2 Q9.5 3 9.5 5.5 Q8 5 7.5 6.5 Q6.5 4.5 7 2 Z" fill="#2e2e2e"/></svg>
        <span>www.quilmora.com</span>
      </li>
    </ul>
  </section>

  <section class="card card--back" aria-label="Business card back">
    <p class="wordmark">quilmora</p>
  </section>
</main>
</body>
</html>
```